KAJU Freightways #ALLKAJU Business Cards & Letterhead

I am looking to business cards designed for our organization. We are currently undergoing a small re-branding that is taking place. Our organization is called KAJU Freightways and we are headquartered in Phoenix, AZ. We primarily provide transportation and logistics services to the Marlow Parcel Bureau who is our largest customer. I would like to see a design that incorporates name, title, contact info, website, and address (this will be different depending on the employee). I would also like to see some color on the business card using our logo colors or a variation. I would like our logo on the back of the business card with the website displayed. The final design should communicate that we are a next generation transportation operate that focuses on being driver-first, customer-centric, innovative, and sustainable.We would also like our #ALLKAJU catch phrase incorporated as well.

Target Market(s)

Transportation & Logistics

Industry/Entity Type

Trucking Company

Contact Information for Business Card

-First and Last Name
-Position Title
-Contact Phone
-Contact Email
-Physical Address

Font styles to use
Serif

Colors

Designer to choose colors to be used in the design.

Requirements
Must have
• -KAJU logo prominently displayed
• -#ALLKAJU catch phrase used
• -Some amount of color, design gradient, etc.
• -Logo on the back with website listed (https://www.kajufreightco.example)

```html
<!DOCTYPE html>
<html lang="en">
<head>
<meta charset="utf-8">
<title>KAJU Freightways – Business Card</title>
<link href="https://fonts.googleapis.com/css2?family=Merriweather:wght@400;700;900&display=swap" rel="stylesheet">
<style>
  :root {
    --teal: #023e48;
    --teal-soft: #0a4a55;
    --green: #7dc242;
    --paper: #fcf7f6;
    --ink: #1a1a1a;
    --divider: #d9d4d3;
    --stage: #3a3a3a;
    --white: #ffffff;
  }
  * { box-sizing: border-box; margin: 0; padding: 0; }
  html, body { width: 1200px; height: 782px; overflow: hidden; }
  body {
    background: var(--stage);
    font-family: "Merriweather", serif;
    display: flex;
    align-items: center;
    justify-content: center;
    gap: 50px;
  }
  .card {
    position: relative;
    width: 540px;
    height: 309px;
    overflow: hidden;
    box-shadow: 0 10px 24px rgba(0,0,0,.45);
  }

  /* Front */
  .card--front { background: var(--paper); }
  .brand-mark {
    position: absolute;
    left: 42px; top: 70px;
    width: 156px; height: 156px;
    border: 6px solid var(--green);
    border-radius: 50%;
    display: flex; align-items: center; justify-content: center;
  }
  .brand-mark__name {
    font-weight: 900;
    font-size: 36px;
    color: var(--teal);
    letter-spacing: 1px;
  }
  .divider {
    position: absolute;
    left: 236px; top: 48px;
    width: 1px; height: 170px;
    background: var(--divider);
  }
  .contact {
    position: absolute;
    left: 260px; top: 52px;
    width: 268px;
    color: var(--ink);
  }
  .contact__name {
    font-weight: 900; font-size: 16px; color: var(--teal);
    letter-spacing: .5px; line-height: 1.2;
  }
  .contact__title { color: var(--green); font-size: 12px; margin-bottom: 8px; }
  .contact__row {
    display: flex; align-items: center; gap: 6px;
    font-size: 12px; line-height: 1.6;
  }
  .contact__row svg { flex: none; }
  .contact__company {
    margin-top: 8px; font-weight: 700; font-size: 12px; color: var(--teal);
    line-height: 1.4;
  }
  .contact__address { font-size: 12px; line-height: 1.45; }
  .bands { position: absolute; left: 0; bottom: 0; }
  .hashtag {
    position: absolute;
    left: 316px; bottom: 9px;
    color: var(--white); font-size: 13px; letter-spacing: .5px;
  }

  /* Back */
  .card--back { background: var(--teal); }
  .pattern-field {
    position: absolute; inset: 0;
    background: linear-gradient(135deg, var(--teal-soft), var(--teal));
  }
  .back-mark {
    position: absolute;
    left: 368px; top: 188px;
    width: 74px; height: 74px;
    border: 3px solid var(--white);
    border-radius: 50%;
    display: flex; align-items: center; justify-content: center;
  }
  .back-mark__name {
    font-weight: 900; font-size: 16px; color: var(--white); letter-spacing: .5px;
  }
  .website {
    position: absolute;
    right: 20px; top: 274px;
    color: var(--white); font-size: 11px; letter-spacing: .3px;
  }
</style>
</head>
<body>

  <section class="card card--front" aria-label="Business card front">
    <div class="brand-mark"><span class="brand-mark__name">KAJU</span></div>
    <div class="divider"></div>

    <div class="contact">
      <p class="contact__name">DANIEL REYES</p>
      <p class="contact__title">Managing Director</p>
      <p class="contact__row">
        <svg width="16" height="16" viewBox="0 0 16 16" aria-hidden="true">
          <circle cx="8" cy="8" r="7.5" fill="var(--green)"/>
          <path d="M4.5 6.2c0-.8 1.6-1.6 3.5-1.6s3.5.8 3.5 1.6v.6h-1.6v-.6H6.1v.6H4.5z M5.3 7.6h5.4l.6 3.4H4.7z" fill="var(--teal)"/>
        </svg>
        044-555 010 246
      </p>
      <p class="contact__row">
        <svg width="16" height="16" viewBox="0 0 16 16" aria-hidden="true">
          <circle cx="8" cy="8" r="7.5" fill="var(--green)"/>
          <rect x="4" y="5" width="8" height="6" fill="var(--teal)"/>
          <path d="M4 5l4 3.4L12 5" fill="none" stroke="#fff" stroke-width="1"/>
        </svg>
        info@kajufreight.example
      </p>
      <p class="contact__company">KAJU Freightways</p>
      <p class="contact__address">88, Harbor Row<br>Phoenix, AZ 85004</p>
    </div>

    <svg class="bands" width="540" height="50" viewBox="0 0 540 50" aria-hidden="true">
      <polygon points="0,22 310,22 310,50 0,50" fill="var(--green)"/>
      <polygon points="290,22 540,22 540,50 300,50" fill="var(--teal)"/>
      <polygon points="300,14 540,14 540,22 290,22" fill="var(--teal)"/>
    </svg>
    <span class="hashtag">#ALLKAJU</span>
  </section>

  <section class="card card--back" aria-label="Business card back">
    <div class="pattern-field" role="img" aria-label="Faint repeating brand-mark pattern in deep teal tones"></div>
    <div class="back-mark"><span class="back-mark__name">KAJU</span></div>
    <p class="website">https://www.kajufreightco.example</p>
  </section>

</body>
</html>
```